Harborline Renewal Business Card Design

Professional and clean design. The design colors should flow with the logo. Two-sided card with the website on the back which is:

www.HarborlineRenewal.example.

"Specializing in Water Damage Restoration"

On the front I need the name, email, phone, and logo.

Name: Darnell Quisby
Email: Darnell@HarborlineRenewal.example
Phone: 555-318-2046 for now

I only have the Preview and Thumbnail right now but should have the source files uploaded within a day or two.

Target Market(s)

Flood victims, home owners with water damage from busted pipes etc...

Industry/Entity Type

Business

Contact Information for Business Card

Name: Darnell Quisby

Font styles to use
Serif
Sans Serif

Requirements
Must have
• Business Card Details Info

```html
<!DOCTYPE html>
<html lang="en">
<head>
<meta charset="utf-8">
<title>Harborline Renewal Business Card</title>
<link rel="stylesheet" href="https://fonts.googleapis.com/css2?family=Open+Sans:wght@400;700&family=Arimo:wght@400&display=swap">
<style>
  :root {
    --page: #e6e8eb;
    --card: #ffffff;
    --blue: #2496d4;
    --blue-light: #56c0ee;
    --ink-white: #ffffff;
    --shadow: rgba(20, 30, 45, 0.18);
  }
  * { margin: 0; padding: 0; box-sizing: border-box; }
  html, body {
    width: 1200px; height: 900px; overflow: hidden;
    background: var(--page);
  }
  .canvas { position: relative; width: 1200px; height: 900px; }
  .card {
    position: absolute; left: 280px;
    width: 640px; height: 366px;
    background: var(--card);
    border-radius: 26px;
    overflow: hidden;
    box-shadow: 0 10px 28px var(--shadow);
  }
  .card-back { top: 52px; }
  .card-front { top: 482px; }

  /* back side */
  .back-mark {
    position: absolute; left: 50%; top: 46px; transform: translateX(-50%);
    display: flex; flex-direction: column; align-items: center; gap: 14px;
  }
  .back-mark .dot {
    width: 150px; height: 150px; border-radius: 50%;
    background: var(--blue);
  }
  .brand-name {
    font-family: "Open Sans", sans-serif; font-weight: 700;
    color: var(--blue); letter-spacing: 0.06em; text-transform: uppercase;
    white-space: nowrap;
  }
  .back-mark .brand-name { font-size: 24px; }
  .back-tagline {
    position: absolute; left: 0; right: 0; top: 276px; text-align: center;
    font-family: "Arimo", sans-serif; color: var(--blue);
    font-size: 17px; letter-spacing: 0.03em; line-height: 1.35;
  }

  /* front side */
  .front-wave { position: absolute; inset: 0; }
  .holder {
    position: absolute; left: 40px; top: 178px;
    font-family: "Open Sans", sans-serif; color: var(--ink-white);
  }
  .holder-name {
    font-weight: 700; font-size: 26px; letter-spacing: 0.02em;
    text-transform: uppercase; margin-bottom: 12px;
  }
  .contact-list { list-style: none; font-size: 16px; line-height: 1.55; }
  .contact-list li { display: flex; align-items: center; gap: 10px; }
  .contact-list svg { width: 13px; height: 13px; flex: none; }
  .front-brand {
    position: absolute; right: 28px; top: 84px; width: 190px;
    display: flex; flex-direction: column; align-items: center; gap: 10px;
    text-align: center;
  }
  .front-brand .dot {
    width: 64px; height: 64px; border-radius: 50%; background: var(--blue);
  }
  .front-brand .brand-name { font-size: 19px; line-height: 1.25; }
</style>
</head>
<body>
<main class="canvas">

  <section class="card card-back" aria-label="Card back">
    <div class="back-mark">
      <span class="dot"></span>
      <span class="brand-name">Harborline Renewal</span>
    </div>
    <p class="back-tagline">SPECIALIZING IN WATER DAMAGE RESTORATION<br>www.HarborlineRenewal.example</p>
  </section>

  <section class="card card-front" aria-label="Card front">
    <svg class="front-wave" viewBox="0 0 640 366" preserveAspectRatio="none" aria-hidden="true">
      <path d="M0 0 H225 C385 40 395 300 300 366 H0 Z" fill="var(--blue)"/>
      <path d="M222 -4 C402 32 412 300 314 370" fill="none" stroke="var(--blue)" stroke-width="4"/>
      <path d="M238 -4 C420 36 426 300 328 370" fill="none" stroke="var(--blue-light)" stroke-width="4"/>
    </svg>
    <div class="holder">
      <p class="holder-name">Darnell Quisby</p>
      <ul class="contact-list">
        <li>
          <svg viewBox="0 0 24 24"><path fill="#fff" d="M6.6 10.8a15 15 0 0 0 6.6 6.6l2.2-2.2c.3-.3.7-.4 1-.2 1.1.4 2.3.6 3.6.6.6 0 1 .4 1 1V20c0 .6-.4 1-1 1A17 17 0 0 1 3 4c0-.6.4-1 1-1h3.5c.6 0 1 .4 1 1 0 1.3.2 2.5.6 3.6.1.3 0 .7-.2 1z"/></svg>
          555-318-2046
        </li>
        <li>
          <svg viewBox="0 0 24 24"><rect x="2.5" y="5" width="19" height="14" rx="1.5" fill="none" stroke="#fff" stroke-width="2"/><path d="M3 6l9 7 9-7" fill="none" stroke="#fff" stroke-width="2"/></svg>
          Darnell@HarborlineRenewal.example
        </li>
        <li>
          <svg viewBox="0 0 24 24"><circle cx="12" cy="12" r="9.5" fill="none" stroke="#fff" stroke-width="2"/><path d="M2.5 12h19M12 2.5c3 3 3 16 0 19M12 2.5c-3 3-3 16 0 19" fill="none" stroke="#fff" stroke-width="1.6"/></svg>
          www.HarborlineRenewal.example
        </li>
      </ul>
    </div>
    <div class="front-brand">
      <span class="dot"></span>
      <span class="brand-name">Harborline<br>Renewal</span>
    </div>
  </section>

</main>
</body>
</html>
```